Vortaleen - Lead the Way!

Vortaleen is a new Silicon Valley company, of the pimrela founders from Berlin, which provides a "Shared Hive Circle". This platform allows the crowd to support startups with money, experts and fame. Our Vision is, that everyone should become an entrepreneur.

Pls find all brief details in the attached document
Updates

Would be nice to have a list of more social services I'm available on, like a list of pictograms of all my services:

Find me on: chattro, fennwix+, qrt, mivrel, datebloom, pohk, rplex, etc...

pls make sure to use the right font:
http://www.typelarder-demo.com/fonts/Orbitron

Target Market(s)

Main target market is those already involved in the startup industry, by fundraising, investing, advising, cofounding and working. Vortaleen brings a totaly new transparency and collaborative way of starting companies to that business.

· Entrepreneurs (looking for funding, team and community)
· Investors (looking for hot investments and )
· Experts (workers looking for startups they can work for equity)
· Incubators & Business Schools (looking for tools to advise startups)

Industry/Entity Type

It Company

Requirements
Must have
• Pls find all brief details in the attached document
Nice to have

```html
<!DOCTYPE html>
<html lang="en">
<head>
<meta charset="utf-8">
<title>Vortaleen business card – front and back</title>
<link rel="stylesheet" href="https://fonts.googleapis.com/css2?family=Orbitron:wght@400;500;700&family=Exo+2:wght@300;400&display=swap">
<style>
  :root {
    --sheet: #1f1b19;
    --frame: #e6e6e6;
    --paper: #ffffff;
    --brand: #e3603b;
    --ink: #4a4a4a;
    --ink-soft: #6a6a6a;
    --label: #b4b4b4;
    --on-brand: #ffffff;
  }
  * { box-sizing: border-box; margin: 0; padding: 0; }
  html, body { width: 1018px; height: 1200px; overflow: hidden; }
  body {
    position: relative;
    background: var(--sheet);
    font-family: "Exo 2", "Orbitron", sans-serif;
    color: var(--ink);
  }
  .card-frame {
    position: absolute;
    left: 93px;
    width: 836px;
    height: 483px;
    background: var(--frame);
  }
  .card-frame--front { top: 76px; }
  .card-frame--back { top: 637px; }
  .card-face {
    position: absolute;
    left: 13px; top: 13px;
    width: 810px; height: 457px;
  }
  .card-face--front { background: var(--paper); }
  .card-face--back { background: var(--brand); }
  .side-tab {
    position: absolute;
    top: 122px;
    width: 28px;
    height: 242px;
    background: var(--brand);
  }
  .side-tab--left { left: 3px; }
  .side-tab--right { right: 1px; }
  .face-label {
    position: absolute;
    left: 95px;
    font-family: "Exo 2", sans-serif;
    font-size: 18px;
    color: var(--label);
  }
  .face-label--front { top: 573px; }
  .face-label--back { top: 1135px; }

  .brand-block {
    position: absolute;
    left: 0; right: 0; top: 200px;
    text-align: center;
  }
  .brand-name {
    font-family: "Orbitron", sans-serif;
    font-weight: 500;
    font-size: 46px;
    color: var(--brand);
    letter-spacing: 1px;
    line-height: 1;
  }
  .brand-tagline {
    font-family: "Exo 2", sans-serif;
    font-weight: 300;
    font-size: 20px;
    color: var(--ink);
    margin-top: 4px;
  }

  .contact-divider {
    position: absolute;
    left: 406px; top: 320px;
    width: 2px; height: 110px;
    background: var(--ink-soft);
  }
  .contact-person, .contact-company {
    position: absolute;
    top: 323px;
    font-size: 11px;
    line-height: 1.05;
  }
  .contact-person { right: 422px; text-align: right; }
  .contact-company { left: 425px; text-align: left; }
  .contact-name, .company-name {
    font-family: "Orbitron", sans-serif;
    font-weight: 700;
    font-size: 18px;
    color: var(--brand);
    letter-spacing: 0.5px;
  }
  .contact-role, .company-tagline {
    font-family: "Orbitron", sans-serif;
    font-size: 13px;
    color: var(--ink);
    margin-top: 4px;
    text-transform: uppercase;
  }
  .contact-web { margin-top: 17px; color: var(--ink); }
  .contact-web .sep { color: var(--brand); }
  .social-list { list-style: none; margin-top: 9px; }
  .social-list li { margin-top: 1px; display: flex; justify-content: flex-end; align-items: center; gap: 6px; }
  .social-mark { width: 7px; height: 7px; background: #5b8fc9; display: inline-block; }
  .company-address { margin-top: 17px; color: var(--ink); }
  .company-phones { margin-top: 12px; color: var(--ink); }
  .company-phones .phone-row { display: flex; align-items: center; gap: 5px; }

  .pitch {
    position: absolute;
    left: 0; right: 0; top: 125px;
    text-align: center;
    color: var(--on-brand);
  }
  .pitch-title {
    font-family: "Orbitron", sans-serif;
    font-weight: 400;
    font-size: 36px;
    letter-spacing: 0.5px;
  }
  .pitch-list {
    list-style: none;
    margin-top: 28px;
    font-size: 17px;
    line-height: 22px;
  }
  .pitch-list li::before { content: "• "; }
  .pitch-cta {
    font-family: "Orbitron", sans-serif;
    font-size: 19px;
    margin-top: 6px;
  }
  .signature-line {
    position: absolute;
    left: 194px; top: 387px;
    width: 419px; height: 2px;
    background: var(--on-brand);
  }
</style>
</head>
<body>
  <div class="card-frame card-frame--front">
    <div class="card-face card-face--front">
      <div class="brand-block">
        <div class="brand-name">Vortaleen</div>
        <div class="brand-tagline">Lead the Way!</div>
      </div>

      <div class="contact-person">
        <div class="contact-name">MARTEN KOLLWEG</div>
        <div class="contact-role">Founder and CEO</div>
        <div class="contact-web">www.vortaleen.com <span class="sep">|</span> hi@vortaleen.com</div>
        <ul class="social-list">
          <li>chirpa.com/martenkollweg <span class="social-mark"></span></li>
          <li>faceloop.com/martenkollweg <span class="social-mark"></span></li>
          <li>linkora.com/in/martenkollweg <span class="social-mark"></span></li>
        </ul>
      </div>

      <div class="contact-divider"></div>

      <div class="contact-company">
        <div class="company-name">VORTALEEN</div>
        <div class="company-tagline">Lead the Way!</div>
        <div class="company-address">
          Berlin – Lindenhof Strasse 14 | 10117 Berlin | Germany<br>
          Silicon Valley – 218 N Calvera Rd | Sunnyvale | CA 94086
        </div>
        <div class="company-phones">
          <div class="phone-row">
            <svg width="12" height="9" viewBox="0 0 12 9" aria-hidden="true"><path d="M1 3 Q6 -1 11 3 L10 4.5 L8 3.5 L8 2.5 Q6 1.8 4 2.5 L4 3.5 L2 4.5 Z M3 5 H9 L10 8.5 H2 Z" fill="#4a4a4a"/></svg>
            mobile 0160 555 204 318 |
          </div>
          <div>phone 0123 555 0147</div>
        </div>
      </div>
    </div>
    <div class="side-tab side-tab--left"></div>
    <div class="side-tab side-tab--right"></div>
  </div>
  <div class="face-label face-label--front">Front</div>

  <div class="card-frame card-frame--back">
    <div class="card-face card-face--back">
      <div class="pitch">
        <h1 class="pitch-title">Are you interested in?</h1>
        <ul class="pitch-list">
          <li>Starting your own Business?</li>
          <li>Investing in hot Startups?</li>
          <li>Working for the next “Faceloop”?</li>
        </ul>
        <p class="pitch-cta">Join us on Faceloop.com/Vortaleen</p>
      </div>
      <div class="signature-line"></div>
    </div>
  </div>
  <div class="face-label face-label--back">Back</div>
</body>
</html>
```